Candle Box & Belly Band Design

Design Candle Box for Soy Candles along with a belly band design that can be used on off the shelf coloured boxes. It is for a premium brand of candle - so i want the packaging to reflect this. I have included must haves below.

The candle boxes will be a few different sizes, but for the purpose of the design it would be something like a cube 12 x 12 x 12 cms

The belly band for standard boxes to be something like 5cm wide on a 12 x 12 x 12cms cube box that goes all the way around the top to the bottom - holding the lid on and providing all the relevant information. Example of box with belly band uploaded

Our company Name : Clover & Jude - our logo is uploaded

Target Market(s)

Premium Candle Buyers

Colors

Designer to choose colors to be used in the design.

Requirements
Must have
• Must have our logo - our logo can be in any colour
• Must state:
• Soy Candle, Hand Poured, Made in Melbourne,
• A space for the fragrance, size and burn time.
• For this project use Lime, Coconut & Elderfllower, 300grams, 50 Hour burn Time

```html
<!DOCTYPE html>
<html lang="en">
<head>
<meta charset="utf-8">
<title>Clover &amp; Jude – Soy Candle Belly Bands</title>
<link href="https://fonts.googleapis.com/css2?family=Open+Sans:wght@400;600;700&display=swap" rel="stylesheet">
<style>
  :root {
    --page: #ffffff;
    --box: #161616;
    --ink: #111111;
    --lime-top: #a6e81f;
    --lime-bottom: #86c42a;
    --coconut-top: #5ec8f2;
    --coconut-bottom: #3aa8e6;
    --elder-top: #f2f78e;
    --elder-bottom: #e3ea78;
  }
  * { box-sizing: border-box; margin: 0; padding: 0; }
  html, body { width: 1200px; height: 1200px; overflow: hidden; background: var(--page); }
  body { font-family: "Open Sans", Arial, sans-serif; color: var(--ink); }

  .range {
    position: absolute; left: 30px; top: 415px;
    display: flex; gap: 30px;
  }
  .box-face {
    position: relative; width: 360px; height: 370px;
    background: var(--box);
    border-radius: 3px;
  }
  .belly-band {
    position: absolute; top: 0; bottom: 0; left: 180px; width: 122px;
    display: flex; flex-direction: column; align-items: center;
    padding-top: 62px;
    background: linear-gradient(180deg, var(--band-top), var(--band-bottom));
  }
  .band--lime { --band-top: var(--lime-top); --band-bottom: var(--lime-bottom); --accent: var(--lime-top); }
  .band--coconut { --band-top: var(--coconut-top); --band-bottom: var(--coconut-bottom); --accent: var(--coconut-top); }
  .band--elder { --band-top: var(--elder-top); --band-bottom: var(--elder-bottom); --accent: var(--elder-top); }

  .brand-mark { width: 30px; height: 30px; border-radius: 50%; background: var(--ink); }
  .brand-name { margin-top: 8px; font-size: 14px; font-weight: 400; letter-spacing: 0.2px; }
  .hand-poured {
    margin-top: 3px; width: 100%;
    background: var(--ink); color: var(--accent);
    font-size: 8px; font-weight: 700; text-align: center; line-height: 11px;
  }
  .product-type { margin-top: 4px; font-size: 13px; font-weight: 600; }

  .spec-list { list-style: none; margin-top: 46px; align-self: flex-start; padding-left: 10px; }
  .spec { display: flex; align-items: center; gap: 4px; font-weight: 600; line-height: 1.55; }
  .spec svg { width: 12px; height: 12px; flex: none; }
  .spec--fragrance { font-size: 13px; font-weight: 700; }
  .spec--detail { font-size: 9.5px; }
  .origin { margin-top: 16px; font-size: 8px; font-weight: 600; }
</style>
</head>
<body>
<main class="range">

  <article class="box-face">
    <section class="belly-band band--lime">
      <span class="brand-mark"></span>
      <p class="brand-name">Clover &amp; Jude</p>
      <p class="hand-poured">HAND POURED</p>
      <h2 class="product-type">Soy Candle</h2>
      <ul class="spec-list">
        <li class="spec spec--fragrance"><svg viewBox="0 0 12 12" fill="none" stroke="#111" stroke-width="1"><rect x="2" y="5" width="6" height="6"/><path d="M5 5V3M5 1.5c.8.6.8 1.2 0 1.5"/></svg>Lime</li>
        <li class="spec spec--detail"><svg viewBox="0 0 12 12" fill="none" stroke="#111" stroke-width="1"><path d="M6 1v10M3 11h6M1 3h10M1 3l-1 4h3zM11 3l-1 4h3z"/></svg>300grams</li>
        <li class="spec spec--detail"><svg viewBox="0 0 12 12" fill="none" stroke="#111" stroke-width="1"><circle cx="6" cy="6" r="5"/><path d="M6 3v3h2.5"/></svg>50 Hour burn Time</li>
      </ul>
      <p class="origin">Made in Melbourne</p>
    </section>
  </article>

  <article class="box-face">
    <section class="belly-band band--coconut">
      <span class="brand-mark"></span>
      <p class="brand-name">Clover &amp; Jude</p>
      <p class="hand-poured">HAND POURED</p>
      <h2 class="product-type">Soy Candle</h2>
      <ul class="spec-list">
        <li class="spec spec--fragrance"><svg viewBox="0 0 12 12" fill="none" stroke="#111" stroke-width="1"><rect x="2" y="5" width="6" height="6"/><path d="M5 5V3M5 1.5c.8.6.8 1.2 0 1.5"/></svg>Coconut</li>
        <li class="spec spec--detail"><svg viewBox="0 0 12 12" fill="none" stroke="#111" stroke-width="1"><path d="M6 1v10M3 11h6M1 3h10M1 3l-1 4h3zM11 3l-1 4h3z"/></svg>300grams</li>
        <li class="spec spec--detail"><svg viewBox="0 0 12 12" fill="none" stroke="#111" stroke-width="1"><circle cx="6" cy="6" r="5"/><path d="M6 3v3h2.5"/></svg>50 Hour burn Time</li>
      </ul>
      <p class="origin">Made in Melbourne</p>
    </section>
  </article>

  <article class="box-face">
    <section class="belly-band band--elder">
      <span class="brand-mark"></span>
      <p class="brand-name">Clover &amp; Jude</p>
      <p class="hand-poured">HAND POURED</p>
      <h2 class="product-type">Soy Candle</h2>
      <ul class="spec-list">
        <li class="spec spec--fragrance"><svg viewBox="0 0 12 12" fill="none" stroke="#111" stroke-width="1"><rect x="2" y="5" width="6" height="6"/><path d="M5 5V3M5 1.5c.8.6.8 1.2 0 1.5"/></svg>Elderfllower</li>
        <li class="spec spec--detail"><svg viewBox="0 0 12 12" fill="none" stroke="#111" stroke-width="1"><path d="M6 1v10M3 11h6M1 3h10M1 3l-1 4h3zM11 3l-1 4h3z"/></svg>300grams</li>
        <li class="spec spec--detail"><svg viewBox="0 0 12 12" fill="none" stroke="#111" stroke-width="1"><circle cx="6" cy="6" r="5"/><path d="M6 3v3h2.5"/></svg>50 Hour burn Time</li>
      </ul>
      <p class="origin">Made in Melbourne</p>
    </section>
  </article>

</main>
</body>
</html>
```